New Bicycle shop business card

Hi!
I'm looking for a business card for my new proffesional bike mechanics shop. This shop is only for fixing broken bikes and not selling bikes.
Peferbly a modern and sleek and modern design.
Colors: black, grey, red, white
Information:
Name: Rijwielwerkplaats Vanhoutte
Shop owner: Bart Vanhoutte & Marieke Segers
Website: www.rijwielwerkplaats-vanhoutte.be
Email: info@rijwielwerkplaats-vanhoutte.be
Phone number: +32471902368
Street adres: Kerkweg 46
9940 Bellebeke
Slogan/shop information: Herstellingen van alle merken.
Logo: see files.
Target Market(s)
People who seek a mechanic to fix or upgrade their bikes.
Contact Information for Business Card
Information:
Website: info@rijwielwerkplaats-vanhoutte.be
9940 Bellebeke
Logo: see files.

```html
<!DOCTYPE html>
<html lang="nl">
<head>
<meta charset="utf-8">
<title>Rijwielwerkplaats Vanhoutte – visitekaartje</title>
<link href="https://fonts.googleapis.com/css2?family=Open+Sans:wght@400;600;700;800&display=swap" rel="stylesheet">
<style>
  :root {
    --red: #ec1f2b;
    --black: #0b0b0c;
    --ink: #231f20;
    --grey: #8f8f8f;
    --white: #ffffff;
    --backdrop: #e9e9e9;
  }
  * { box-sizing: border-box; margin: 0; padding: 0; }
  html, body { width: 1200px; height: 1200px; overflow: hidden; }
  body {
    background: var(--backdrop);
    font-family: "Open Sans", Arial, sans-serif;
    position: relative;
  }
  .card {
    position: absolute;
    left: 240px;
    width: 720px;
    height: 420px;
    overflow: hidden;
  }
  .card-front { top: 142px; background: var(--white); }
  .card-back { top: 637px; background: var(--red); }

  .brand {
    position: absolute;
    display: flex;
    flex-direction: column;
    align-items: center;
    text-align: center;
  }
  .brand-dot {
    width: 64px; height: 64px;
    border-radius: 50%;
    margin-bottom: 18px;
  }
  .brand-name {
    font-weight: 800;
    color: var(--ink);
    line-height: 1.15;
    letter-spacing: 0.5px;
  }
  .card-front .brand { left: 30px; width: 300px; top: 128px; }
  .card-front .brand-dot { background: var(--red); }
  .card-front .brand-name { font-size: 24px; }

  .divider {
    position: absolute;
    left: 359px; top: 114px;
    width: 2px; height: 186px;
    background: var(--red);
  }
  .details { position: absolute; left: 392px; top: 108px; }
  .label { color: var(--red); font-weight: 600; font-size: 18px; line-height: 1.2; }
  .owners { color: var(--grey); font-weight: 700; font-size: 20px; line-height: 1.3; }
  .shop-name { color: var(--red); font-weight: 700; font-size: 20px; margin-top: 10px; line-height: 1.3; }
  .role { color: var(--black); font-weight: 600; font-size: 15.5px; line-height: 1.4; }
  .contact { list-style: none; margin-top: 16px; }
  .contact li {
    display: flex; align-items: center; gap: 10px;
    color: var(--grey); font-size: 17px; line-height: 23.5px;
  }
  .contact svg { width: 12px; height: 12px; flex: none; fill: var(--red); }

  .footer-curve { position: absolute; left: 0; bottom: 0; width: 720px; height: 70px; }
  .address {
    position: absolute; left: 0; right: 0; bottom: 14px;
    text-align: center; color: var(--white); font-size: 17px;
  }

  .card-back .brand { left: 0; right: 0; top: 110px; }
  .card-back .brand-dot { background: var(--white); width: 80px; height: 80px; margin-bottom: 22px; }
  .card-back .brand-name { font-size: 34px; }
  .tagline {
    position: absolute; left: 0; right: 0; top: 374px;
    text-align: center; color: var(--white); font-weight: 700; font-size: 16px;
  }
</style>
</head>
<body>
  <section class="card card-front">
    <div class="brand">
      <span class="brand-dot"></span>
      <p class="brand-name">RIJWIELWERKPLAATS<br>VANHOUTTE</p>
    </div>
    <div class="divider"></div>
    <div class="details">
      <p class="label">Shop owner:</p>
      <p class="owners">Bart Vanhoutte &amp; Marieke Segers</p>
      <p class="shop-name">Rijwielwerkplaats Vanhoutte</p>
      <p class="role">General Manager</p>
      <ul class="contact">
        <li><svg viewBox="0 0 24 24"><path d="M6.6 10.8a15 15 0 0 0 6.6 6.6l2.2-2.2c.3-.3.7-.4 1-.2 1.1.4 2.3.6 3.6.6.6 0 1 .4 1 1V20c0 .6-.4 1-1 1A17 17 0 0 1 3 4c0-.6.4-1 1-1h3.5c.6 0 1 .4 1 1 0 1.3.2 2.5.6 3.6.1.3 0 .7-.2 1z"/></svg>+32471902368</li>
        <li><svg viewBox="0 0 24 24"><path d="M2 5h20v14H2z M2 5l10 8 10-8" /></svg>info@rijwielwerkplaats-vanhoutte.be</li>
        <li><svg viewBox="0 0 24 24"><circle cx="12" cy="12" r="10"/></svg>www.rijwielwerkplaats-vanhoutte.be</li>
      </ul>
    </div>
    <svg class="footer-curve" viewBox="0 0 720 70" preserveAspectRatio="none">
      <path d="M0 38 Q360 -12 720 38 Q360 2 0 38 Z" fill="var(--red)"/>
      <path d="M0 70 L0 48 Q360 -2 720 48 L720 70 Z" fill="var(--black)"/>
    </svg>
    <p class="address">Kerkweg 46 9940 Bellebeke</p>
  </section>

  <section class="card card-back">
    <div class="brand">
      <span class="brand-dot"></span>
      <p class="brand-name">RIJWIELWERKPLAATS<br>VANHOUTTE</p>
    </div>
    <p class="tagline">Herstellingen van alle merken.</p>
  </section>
</body>
</html>
```